Need website for LED Signs company

Need an web page for a sign company. Basic home page / Tab for photo gallery (projects), tab for other projects could be photo gallery type with the ability for descriptions gallery to be able to have albums (projects) and tab for about us / testimonials Should be easy for me to change with dreamweaver or easy to change add remove content. I will provide pictures and content I would be happy if it could be set up like a template where i can add the content after but i would provide as much content as possible the current page is http://glowcrestsigns.ca examples of my competition:https://metroled.com/led-message-signs/http://www.libertevision.com/https://www.daktronics.com/en-us/products/message-displaysSEO optimized

1 page

• I want to feature LED signs and EMC's the Special projects tab tab will or should be a photo type gallery that is easy to add photos with detailed descriptions
• I do not want to wast peoples time making something similar to what i have now.
• To help me pick a winner Please show links to some of the sites you have created in the past. .

```html
<!DOCTYPE html>
<html lang="en">
<head>
<meta charset="utf-8">
<title>GlowCrest Signs — The Future of L.E.D Technology</title>
<link rel="stylesheet" href="https://fonts.googleapis.com/css2?family=Montserrat:wght@400;500;600;700&family=Lato:wght@400;700&display=swap">
<style>
:root{
  --blue:#0b5de3;
  --blue-bright:#1f6ff2;
  --ink:#111318;
  --text:#222;
  --muted:#666;
  --line:#d9d9d9;
  --dark:#151515;
  --dark-2:#1c1c1c;
  --white:#fff;
}
*{margin:0;padding:0;box-sizing:border-box}
html,body{width:1200px;height:5056px;overflow:hidden}
body{font-family:"Lato",sans-serif;color:var(--text);background:var(--white);position:relative}
section,header,footer{position:absolute;left:0;width:1200px}
.abs{position:absolute}
.center{left:0;width:1200px;text-align:center}
.heading{font-family:"Montserrat",sans-serif}
.eyebrow{font-family:"Montserrat",sans-serif;font-size:17px;font-weight:600;letter-spacing:1px;color:var(--blue);text-transform:uppercase}

/* Hero */
.hero{top:0;height:675px;overflow:hidden}
.hero-photo{position:absolute;inset:0;background:
  radial-gradient(ellipse at 55% 35%,rgba(210,60,70,.55),transparent 45%),
  radial-gradient(ellipse at 30% 80%,rgba(40,90,160,.5),transparent 50%),
  radial-gradient(ellipse at 80% 70%,rgba(220,140,60,.35),transparent 45%),
  linear-gradient(180deg,#0e1118 0%,#2a1c24 45%,#1a1f2c 100%)}
.hero-shade{position:absolute;inset:0;background:rgba(0,0,0,.35)}
.logo{left:78px;top:30px;font-family:"Montserrat",sans-serif;font-weight:700;font-size:26px;color:var(--white);letter-spacing:.5px}
.nav{right:78px;top:40px;display:flex;gap:26px;font-family:"Montserrat",sans-serif;font-size:13px;font-weight:500;color:var(--white)}
.nav a{color:inherit;text-decoration:none}
.nav .active{color:var(--blue-bright);border-bottom:2px solid var(--blue-bright);padding-bottom:4px}
.hero-title{top:208px;font-family:"Montserrat",sans-serif;font-weight:700;font-size:60px;line-height:72px;color:var(--white)}
.hero-sub{top:384px;font-family:"Montserrat",sans-serif;font-weight:600;font-size:17px;color:var(--white);letter-spacing:.5px}
.hero-buttons{top:472px;left:0;width:1200px;display:flex;justify-content:center;gap:20px}
.btn{display:inline-block;width:236px;height:62px;line-height:62px;text-align:center;font-family:"Montserrat",sans-serif;font-weight:600;font-size:14px;color:var(--white);text-decoration:none}
.btn-blue{background:var(--blue)}
.btn-dark{background:#1a1a1a}

/* Welcome */
.welcome{top:675px;height:589px;background:var(--white)}
.welcome .eyebrow{left:81px;top:74px}
.welcome-title{left:81px;top:118px;width:1040px;font-size:40px;line-height:56px;font-weight:600;color:var(--ink)}
.welcome-copy{left:81px;top:246px;width:1040px;font-size:13px;line-height:22px;color:var(--text)}
.feature{top:372px;width:520px;height:150px}
.feature svg{position:absolute;left:0;top:4px}
.feature h3{position:absolute;left:62px;top:0;font-family:"Montserrat",sans-serif;font-size:22px;font-weight:600;color:var(--ink)}
.feature p{position:absolute;left:62px;top:36px;width:450px;font-size:13px;line-height:22px;color:var(--muted)}
.feature a{position:absolute;left:62px;top:114px;font-family:"Montserrat",sans-serif;font-size:13px;font-weight:700;color:var(--blue);text-decoration:none}

/* Gallery */
.gallery{top:1264px;height:1921px;background:linear-gradient(90deg,var(--dark) 0 50%,var(--dark-2) 50% 100%)}
.gallery .eyebrow{top:90px}
.gallery-title{top:148px;left:240px;width:720px;text-align:center;font-size:40px;line-height:56px;font-weight:500;color:var(--white)}
.tile{position:absolute}
.tile-1{left:81px;top:387px;width:519px;height:462px;background:radial-gradient(ellipse at 55% 40%,#c94fd8,transparent 55%),linear-gradient(180deg,#3d1c5e,#6b3d8a 60%,#4a3a6a)}
.tile-2{left:600px;top:387px;width:519px;height:523px;background:radial-gradient(ellipse at 55% 55%,#e04fb5,transparent 50%),linear-gradient(135deg,#3a2b1e,#1a1410 60%,#3d2e20)}
.tile-3{left:81px;top:849px;width:519px;height:438px;background:linear-gradient(180deg,#2a1626,#160c14)}
.tile-4{left:600px;top:987px;width:519px;height:472px;background:radial-gradient(ellipse at 50% 50%,#d4823e,transparent 60%),linear-gradient(135deg,#2d4d8a,#8c3a2a 60%,#c8702e)}
.tile-5{left:81px;top:1287px;width:519px;height:533px;background:linear-gradient(180deg,#5b6070 0%,#3c6aa8 55%,#b0c0d8 100%)}
.tile-6{left:600px;top:1459px;width:519px;height:361px;background:linear-gradient(180deg,#b9b9b0 0%,#6a8a4a 45%,#7a5a3a 75%,#3a5a4a 100%)}
.tile-overlay{position:absolute;inset:0;background:rgba(0,0,0,.45)}
.tile-link{position:absolute;left:24px;top:24px;width:52px;height:52px;border:2px solid rgba(255,255,255,.7);border-radius:50%}
.tile-link svg{position:absolute;left:13px;top:13px}
.tile-dots{position:absolute;left:0;width:100%;top:200px;text-align:center;color:var(--white);font-size:20px;letter-spacing:2px}
.tile-caption{position:absolute;left:24px;bottom:48px;font-family:"Montserrat",sans-serif;font-size:16px;font-weight:600;color:var(--white)}

/* Markets */
.markets{top:3185px;height:539px;background:var(--white)}
.markets .eyebrow{top:70px}
.markets-title{top:124px;left:300px;width:600px;text-align:center;font-size:40px;line-height:56px;font-weight:500;color:var(--ink)}
.market-row{left:81px;top:270px;display:flex;gap:24px}
.market{width:189px;height:189px;border:1px solid var(--line);position:relative;text-align:center}
.market svg{position:absolute;left:69px;top:42px}
.market span{position:absolute;left:0;width:100%;top:120px;font-family:"Montserrat",sans-serif;font-size:14px;font-weight:500;color:var(--ink)}

/* Testimonial */
.testimonial{top:3724px;height:539px;overflow:hidden}
.testimonial-bg{position:absolute;inset:0;background:
  radial-gradient(ellipse at 95% 20%,rgba(120,110,60,.45),transparent 40%),
  radial-gradient(ellipse at 5% 80%,rgba(90,80,60,.35),transparent 40%),
  linear-gradient(180deg,#0c0c0c,#161616)}
.quote-mark{left:558px;top:82px}
.testimonial-text{top:152px;left:190px;width:820px;text-align:center;font-family:"Montserrat",sans-serif;font-size:30px;line-height:46px;font-weight:500;color:var(--white)}
.client{top:366px;font-family:"Montserrat",sans-serif;font-size:17px;font-weight:600;color:var(--blue-bright);letter-spacing:1px}
.dots{top:444px;left:0;width:1200px;display:flex;justify-content:center;gap:8px}
.dots i{display:block;width:32px;height:3px;background:rgba(255,255,255,.25)}
.dots i.on{background:var(--white)}

/* Contact */
.contact{top:4263px;height:793px;background:var(--blue);color:var(--white)}
.contact .eyebrow{top:66px;color:var(--white)}
.contact-title{top:118px;left:250px;width:700px;text-align:center;font-size:38px;line-height:56px;font-weight:600}
.email{top:276px;font-family:"Montserrat",sans-serif;font-size:62px;font-weight:500}
.rule-short{left:400px;top:418px;width:400px;height:1px;background:rgba(255,255,255,.35)}
.address{top:460px;font-size:24px;line-height:40px;color:rgba(255,255,255,.9);font-style:normal}
.rule-long{left:81px;top:632px;width:1038px;height:1px;background:rgba(255,255,255,.35)}
.btn-top{left:492px;top:648px;width:216px;height:52px;line-height:52px;background:rgba(255,255,255,.18);font-size:14px;font-weight:500;text-align:center;font-family:"Montserrat",sans-serif;color:var(--white);text-decoration:none}
.copyright{top:738px;font-size:13px;color:rgba(255,255,255,.85)}
</style>
</head>
<body>

<header class="hero">
  <div class="hero-photo" role="img" aria-label="Night photo of a neon-lit roadside diner sign glowing red and blue"></div>
  <div class="hero-shade"></div>
  <div class="abs logo">GLOWCREST SIGNS</div>
  <nav class="abs nav">
    <a class="active" href="#">HOME</a><a href="#">ABOUT</a><a href="#">SERVICES</a><a href="#">GALLERY</a><a href="#">DOWNLOADS</a><a href="#">TECHNOLOGY</a><a href="#">TESTIMONIALS</a><a href="#">CONTACT</a>
  </nav>
  <h1 class="abs center hero-title">THE FUTURE OF<br>L.E.D TECHNOLOGY</h1>
  <div class="abs center hero-sub">GLOWCREST SIGNS</div>
  <div class="abs hero-buttons">
    <a class="btn btn-blue" href="#">MORE ABOUT US</a>
    <a class="btn btn-dark" href="#">CONTACT US</a>
  </div>
</header>

<section class="welcome">
  <div class="abs eyebrow">Welcome to GlowCrest Signs</div>
  <h2 class="abs heading welcome-title">Our strong manufacturing team will transform your ideas into L.E.D. works of art.</h2>
  <p class="abs welcome-copy">GlowCrest Signs is not your average L.E.D. company. Our technology and custom made LED modules have what it takes to make your custom project come to life. Our team will work with you to create your wildest projects. No project is too big or too small. From digital signage, video walls, window signs or custom made LED booths, GlowCrest Signs will exceed your expectations.</p>

  <div class="abs feature" style="left:81px">
    <svg width="44" height="44" viewBox="0 0 24 24" fill="none" stroke="#0b5de3" stroke-width="1.4"><circle cx="12" cy="12" r="3.2"/><path d="M12 2.5l1.6 2.3 2.7-.8.5 2.8 2.7.9-.9 2.6 2 2-2 2 .9 2.6-2.7.9-.5 2.8-2.7-.8L12 21.5l-1.6-2.3-2.7.8-.5-2.8-2.7-.9.9-2.6-2-2 2-2-.9-2.6 2.7-.9.5-2.8 2.7.8z"/></svg>
    <h3>SERVICES</h3>
    <p>We are a custom build service. If you can dream it, we can build it. From outdoor displays in your back yard, to massive video walls for indoor and outdoor applications.</p>
    <a href="#">KNOW MORE ⟶</a>
  </div>
  <div class="abs feature" style="left:627px">
    <svg width="44" height="44" viewBox="0 0 24 24" fill="none" stroke="#0b5de3" stroke-width="1.4"><rect x="6" y="6" width="12" height="12" rx="1"/><rect x="9" y="9" width="6" height="6"/><path d="M9 2v4M12 2v4M15 2v4M9 18v4M12 18v4M15 18v4M2 9h4M2 12h4M2 15h4M18 9h4M18 12h4M18 15h4"/></svg>
    <h3>TECHNOLOGY</h3>
    <p>SMD leds are the leading technology for LED Displays, now whether it is for indoor or outdoor LED Display/EMC Displays. Check with your manufacturer if they still use the old DIP.</p>
    <a href="#">KNOW MORE ⟶</a>
  </div>
</section>

<section class="gallery">
  <div class="abs center eyebrow">Project Gallery</div>
  <h2 class="abs heading gallery-title">more natural look and feel of an image on an LED Display being much less pixilated</h2>

  <div class="tile tile-1" role="img" aria-label="Children's bedroom with a purple-lit hexagon LED wall feature"></div>
  <div class="tile tile-2" role="img" aria-label="Pink LED scrolling sign reading Welcome in a shop window"></div>
  <div class="tile tile-3" role="img" aria-label="Dark project photo of an LED installation">
    <div class="tile-overlay"></div>
    <div class="tile-link"><svg width="22" height="22" viewBox="0 0 24 24" fill="none" stroke="#fff" stroke-width="2"><path d="M10 14a4 4 0 0 0 5.7 0l3-3a4 4 0 0 0-5.7-5.7l-1 1"/><path d="M14 10a4 4 0 0 0-5.7 0l-3 3a4 4 0 0 0 5.7 5.7l1-1"/></svg></div>
    <div class="tile-dots">•••</div>
    <div class="tile-caption">LOREM IPSUM</div>
  </div>
  <div class="tile tile-4" role="img" aria-label="Colourful lion artwork shown on a high-resolution LED display"></div>
  <div class="tile tile-5" role="img" aria-label="Trade show LED cube booth showing video content"></div>
  <div class="tile tile-6" role="img" aria-label="Outdoor LED video screen beside a backyard pool and fire feature"></div>
</section>

<section class="markets">
  <div class="abs center eyebrow">Find Your Market</div>
  <h2 class="abs heading markets-title">We have come up with the magic combination.</h2>
  <div class="abs market-row">
    <div class="market">
      <svg width="50" height="50" viewBox="0 0 24 24" fill="none" stroke="#999" stroke-width="1.2"><path d="M12 20s-7-4.5-7-10a4 4 0 0 1 7-2.6A4 4 0 0 1 19 10c0 5.5-7 10-7 10z"/><path d="M6 12h3l1.5-2.5 2 5 1.5-2.5H18"/></svg>
      <span>HEALTH</span>
    </div>
    <div class="market">
      <svg width="50" height="50" viewBox="0 0 24 24" fill="none" stroke="#999" stroke-width="1.2"><path d="M3 6v13M21 13v6M3 16h18M3 13h18v-3a2 2 0 0 0-2-2H9v5"/><rect x="4.5" y="9.5" width="3.5" height="3" rx="1"/></svg>
      <span>HOTEL</span>
    </div>
    <div class="market">
      <svg width="50" height="50" viewBox="0 0 24 24" fill="none" stroke="#0b5de3" stroke-width="1.2"><circle cx="12" cy="8" r="4"/><path d="M4 21c0-4.4 3.6-7 8-7s8 2.6 8 7"/><path d="M11 14l1 3 1-3"/></svg>
      <span>ORGANIZATION</span>
    </div>
    <div class="market">
      <svg width="50" height="50" viewBox="0 0 24 24" fill="none" stroke="#999" stroke-width="1.2"><path d="M4 17a8 8 0 0 1 16 0z"/><path d="M2 19h20M12 7V5M10.5 5h3"/></svg>
      <span>RESTAURANT</span>
    </div>
    <div class="market">
      <svg width="50" height="50" viewBox="0 0 24 24" fill="none" stroke="#999" stroke-width="1.2"><circle cx="12" cy="12" r="9"/><path d="M3 12h18M12 3v18M5.6 5.6c3 3 3 9.8 0 12.8M18.4 5.6c-3 3-3 9.8 0 12.8"/></svg>
      <span>SPORT</span>
    </div>
  </div>
</section>

<section class="testimonial">
  <div class="testimonial-bg" role="img" aria-label="Dark background of glowing LED pixel panels"></div>
  <svg class="abs quote-mark" width="84" height="50" viewBox="0 0 84 50" fill="none" stroke="#1f6ff2" stroke-width="3"><path d="M4 4h30v26H22l-8 14V30H4z"/><path d="M50 4h30v26H68l-8 14V30H50z"/></svg>
  <p class="abs testimonial-text">Lorem Ipsum is simply dummy text of the printing and typesetting industry. Lorem Ipsum has been the industry's standard dummy text ever since the 1500s, when an unknown printer took.</p>
  <div class="abs center client">- CLIENT NAME</div>
  <div class="abs dots"><i class="on"></i><i></i><i></i><i></i></div>
</section>

<footer class="contact">
  <div class="abs center eyebrow">Keep in Touch</div>
  <h2 class="abs heading contact-title">Tell us about it, we would be happy to provide you with an estimate</h2>
  <div class="abs center email">sales@glowcrestsigns.ca</div>
  <div class="abs rule-short"></div>
  <address class="abs center address">Harrowfield, Saskatchewan S4X<br>2K7 Canada<br>(306) 555-0148</address>
  <div class="abs rule-long"></div>
  <a class="abs btn-top" href="#">BACK TO TOP</a>
  <div class="abs center copyright">©GLOWCREST SIGNS, 2019 - All Rights Reserved.</div>
</footer>

</body>
</html>
```